RTavenor Business Cards & Letterhead

I have a logo but need a design for some new business cards. We are a Design-Build Firm that specializes in the design and construction of commercial projects.
the cards need to be professional. no cartoon stuff.
i would like to have the cards in AI format so I can update the card as needed. Logo is provided.
Our Address is: 4187 Marlowe Ct. Maplecrest, Rivermont 27614

```html
<!DOCTYPE html>
<html lang="en">
<head>
<meta charset="UTF-8">
<title>RTavenor Business Card</title>
<link href="https://fonts.googleapis.com/css2?family=Montserrat:wght@400;500;700;800&family=Montserrat+Alternates:wght@700&display=swap" rel="stylesheet">
<style>
  :root {
    --page-bg: #d9dadc;
    --brand-blue: #135f95;
    --blue-light: #6aa3c6;
    --blue-mid: #1f77ad;
    --blue-deep: #14598f;
    --ink-grey: #5c5d60;
    --text-dark: #3c3d40;
    --rule: #555659;
  }
  * { margin: 0; padding: 0; box-sizing: border-box; }
  html, body { width: 1200px; height: 1200px; overflow: hidden; }
  body {
    background: var(--page-bg);
    font-family: "Montserrat", Arial, sans-serif;
    position: relative;
  }
  .card {
    position: absolute;
    left: 190px;
    width: 820px;
    height: 470px;
    border-radius: 28px;
    box-shadow: 0 6px 18px rgba(0,0,0,0.18);
    overflow: hidden;
  }
  .card-front {
    top: 95px;
    background: linear-gradient(135deg, var(--blue-light) 0%, var(--blue-mid) 50%, var(--blue-deep) 100%);
    display: flex;
    align-items: center;
    justify-content: center;
  }
  .wordmark {
    font-family: "Montserrat", Arial, sans-serif;
    font-weight: 800;
    letter-spacing: 2px;
    display: flex;
    align-items: center;
    gap: 16px;
    white-space: nowrap;
  }
  .wordmark-square { display: inline-block; }
  .card-front .wordmark { color: #ffffff; font-size: 78px; }
  .card-front .wordmark-square { width: 54px; height: 54px; background: #ffffff; }
  .card-back { top: 635px; background: linear-gradient(135deg, #f4f4f4 0%, #e9e9ea 100%); }
  .card-back .wordmark {
    position: absolute; left: 66px; top: 70px;
    color: var(--ink-grey); font-size: 40px; gap: 10px;
  }
  .card-back .wordmark-square { width: 30px; height: 30px; background: var(--ink-grey); }
  .person-name {
    position: absolute; right: 60px; top: 150px;
    font-family: "Montserrat Alternates", "Montserrat", sans-serif;
    font-weight: 700; font-size: 34px; color: var(--brand-blue); letter-spacing: 1px;
    white-space: nowrap;
  }
  .person-title {
    position: absolute; right: 60px; top: 198px;
    font-size: 19px; color: var(--text-dark); letter-spacing: 0.5px;
  }
  .divider {
    position: absolute; left: 110px; top: 215px; width: 535px; height: 2px; background: var(--rule);
  }
  .contacts {
    position: absolute; left: 110px; top: 290px; list-style: none;
  }
  .contacts li {
    display: flex; align-items: center; gap: 14px;
    font-size: 21px; color: var(--text-dark); height: 38px; white-space: nowrap;
  }
  .contacts svg { width: 20px; height: 20px; flex: none; }
  .address {
    position: absolute; right: 60px; top: 300px; text-align: right;
    font-size: 21px; color: var(--text-dark); line-height: 1.45; white-space: nowrap;
  }
</style>
</head>
<body>
  <section class="card card-front">
    <div class="wordmark"><span class="wordmark-square"></span>RTAVENOR</div>
  </section>

  <section class="card card-back">
    <div class="wordmark"><span class="wordmark-square"></span>RTAVENOR</div>

    <div class="person-name">Marcus Tavenor</div>
    <div class="person-title">President</div>

    <div class="divider"></div>

    <ul class="contacts">
      <li>
        <svg viewBox="0 0 24 24" aria-hidden="true"><path fill="#135f95" d="M6.6 10.8a15.1 15.1 0 0 0 6.6 6.6l2.2-2.2a1 1 0 0 1 1-.25 11.4 11.4 0 0 0 3.6.57 1 1 0 0 1 1 1V20a1 1 0 0 1-1 1A17 17 0 0 1 3 4a1 1 0 0 1 1-1h3.5a1 1 0 0 1 1 1c0 1.25.2 2.45.57 3.57a1 1 0 0 1-.25 1z"/></svg>
        (919)-555-0142
      </li>
      <li>
        <svg viewBox="0 0 24 24" aria-hidden="true"><rect x="2" y="5" width="20" height="14" rx="1.5" fill="#135f95"/><path d="M3 6l9 7 9-7" fill="none" stroke="#f1f1f1" stroke-width="1.6"/></svg>
        info@rtavenor.com
      </li>
      <li>
        <svg viewBox="0 0 24 24" aria-hidden="true"><circle cx="12" cy="12" r="10" fill="#135f95"/><g fill="none" stroke="#f1f1f1" stroke-width="1.3"><ellipse cx="12" cy="12" rx="4" ry="10"/><path d="M2 12h20M4 7h16M4 17h16"/></g></svg>
        www.rtavenor.com
      </li>
    </ul>

    <div class="address">
      4187 Marlowe Ct. Maplecrest,<br>
      Rivermont 27614
    </div>
  </section>
</body>
</html>
```